Quillfield Air Business Card Design

Design new, 2 sides, business cards for a residential and light commercial heating, air conditioning contractor.

Target Market(s)

Homeowners, small businesses

Industry/Entity Type

Business

Contact Information for Business Card

Dominic Westerhall
Phone - 862-415-2736
Email
Address - PO box 518
Brightwater NJ 07912
Website - www.HarborBreezeLLC.example

Requirements
Must have
• logo, company colors, standard size with no die cut, so I can use nova stamp

```html
<!DOCTYPE html>
<html lang="en">
<head>
<meta charset="utf-8">
<title>Quillfield Air Business Card</title>
<link rel="stylesheet" href="https://fonts.googleapis.com/css2?family=Montserrat:wght@700&family=Open+Sans:wght@400;600;700&family=Tinos&display=swap">
<style>
  :root {
    --stage: #6e0b1a;
    --crimson: #7f0d20;
    --paper: #f0f0ef;
    --white: #ffffff;
    --orange: #e8902a;
    --ink: #1c1c1c;
  }
  * { box-sizing: border-box; margin: 0; padding: 0; }
  html, body { width: 1200px; height: 987px; overflow: hidden; }
  body {
    background: var(--stage);
    position: relative;
    font-family: "Open Sans", Arial, sans-serif;
  }
  .card {
    position: absolute;
    width: 352px;
    height: 612px;
    box-shadow: 0 6px 18px rgba(0,0,0,0.35);
  }
  .card--front { left: 231px; top: 209px; background: var(--crimson); color: var(--white); }
  .card--back { left: 616px; top: 252px; background: var(--paper); color: var(--ink); }

  .contact {
    position: absolute;
    top: 80px;
    left: 0;
    width: 100%;
    padding: 0 16px;
    text-align: center;
    font-size: 15.5px;
    line-height: 1.32;
  }
  .contact__name {
    font-family: "Montserrat", Arial, sans-serif;
    font-weight: 700;
    font-size: 24px;
    letter-spacing: 0.5px;
    line-height: 1.2;
    white-space: nowrap;
  }
  .contact__title { font-size: 16px; letter-spacing: 0.5px; }
  .contact__group { margin-top: 10px; }
  .contact__label { color: var(--orange); font-weight: 600; }

  .brand {
    position: absolute;
    left: 0;
    width: 100%;
    display: flex;
    align-items: center;
    justify-content: center;
    gap: 12px;
    font-family: "Open Sans", Arial, sans-serif;
    font-weight: 700;
    font-size: 34px;
    line-height: 1.2;
    white-space: nowrap;
  }
  .brand__dot {
    width: 22px;
    height: 22px;
    border-radius: 50%;
    background: var(--orange);
    flex: none;
  }
  .card--front .brand { top: 440px; color: var(--white); }
  .card--back .brand { top: 284px; color: var(--crimson); }

  .tagline {
    position: absolute;
    top: 494px;
    left: 0;
    width: 100%;
    text-align: center;
    font-family: "Tinos", "Times New Roman", serif;
    font-size: 17px;
    line-height: 1.25;
  }
</style>
</head>
<body>
  <section class="card card--front" aria-label="Business card front">
    <div class="contact">
      <p class="contact__name">DOMINIC WESTERHALL</p>
      <p class="contact__title">CEO/FOUNDER</p>
      <p>dominic@quillfieldairllc.example</p>
      <div class="contact__group">
        <p><span class="contact__label">(P)</span> 862 415 2736 <span class="contact__label">(M)</span> 862 415 2790</p>
        <p><span class="contact__label">(F)</span> 862 415 2741</p>
      </div>
      <div class="contact__group">
        <p>PO box 518</p>
        <p>Brightwater NJ 07912</p>
      </div>
      <p class="contact__group">www.QuillfieldAirLLC.example</p>
    </div>
    <div class="brand"><span class="brand__dot"></span><span>Quillfield Air</span></div>
  </section>

  <section class="card card--back" aria-label="Business card back">
    <div class="brand"><span class="brand__dot"></span><span>Quillfield Air</span></div>
    <p class="tagline">Residential &amp; light<br>commercial heating<br>Air conditioning contractor</p>
  </section>
</body>
</html>
```